Banner Graphics For Veltrin Storefront Page

Hello,
I am looking for a designer to help me with a banner heading that I want to place on my Veltrin storefront page. My company sells outdoor kitchen/bbq island accessories. I would like for it to have a background photo with text/logo & graphics overlaid on the image. If possible I would like it to include the 5 small "benefit boxes" that are attached on the file that features graphics for one of the products that I sell . I have also included a color photo of my products in actual use. Feel free to use it but if you have a better idea of a background image feel free to try it, maybe a lifestyle stock photo?? Or maybe something else?? I am open to all ideas and you are the creative ones:) Feel free to be creative. The pixel requirements for final image is 3,000 pixels by 600 pixels. Let me know if you have any questions. THANKS! P.s. I also included some stock photos that I like to give you some ideas.

```html
<!DOCTYPE html>
<html lang="en">
<head>
<meta charset="utf-8">
<title>Crestline Outdoor Kitchens – Storefront Banners</title>
<link href="https://fonts.googleapis.com/css2?family=Cinzel:wght@400;600&family=Open+Sans:wght@400&display=swap" rel="stylesheet">
<style>
  :root {
    --stage-light: #8c8c8c;
    --stage-dark: #555555;
    --ink: #151515;
    --panel: #0d0d0d;
    --white: #ffffff;
    --soft: #d6d6d6;
    --badge: #e9e9e9;
    --warm-1: #c9a469;
    --warm-2: #6f7a3a;
    --wood-1: #3a2a1e;
    --wood-2: #1c1612;
  }
  * { box-sizing: border-box; margin: 0; padding: 0; }
  html, body { width: 1200px; height: 1200px; overflow: hidden; }
  body {
    position: relative;
    background: radial-gradient(ellipse at 50% 20%, var(--stage-light), var(--stage-dark) 80%);
    font-family: "Open Sans", sans-serif;
  }
  .banner {
    position: absolute;
    left: 66px;
    width: 1068px;
    height: 214px;
    overflow: hidden;
    background: var(--ink);
    color: var(--white);
  }
  .banner--lifestyle { top: 182px; }
  .banner--doors { top: 494px; }
  .banner--accessories { top: 804px; }

  .banner-art { position: absolute; top: 0; left: 0; }

  /* brand wordmark */
  .brand { position: absolute; text-align: center; color: var(--white); }
  .brand-name {
    font-family: "Cinzel", serif;
    font-weight: 400;
    font-size: 34px;
    line-height: 1;
    letter-spacing: 0.5px;
    white-space: nowrap;
  }
  .brand-line {
    font-family: "Cinzel", serif;
    font-size: 10px;
    letter-spacing: 2px;
    margin-top: 6px;
    white-space: nowrap;
  }
  .brand-quote {
    font-family: "Cinzel", serif;
    font-size: 12px;
    line-height: 1.3;
    text-align: left;
    margin-top: 24px;
  }

  /* headlines */
  .headline {
    position: absolute;
    font-family: "Cinzel", serif;
    font-weight: 600;
    text-transform: uppercase;
    white-space: nowrap;
  }
  .subline {
    position: absolute;
    font-family: "Cinzel", serif;
    text-transform: uppercase;
    white-space: nowrap;
  }

  /* lifestyle banner */
  .banner--lifestyle .headline {
    left: 450px; right: 0; top: 10px;
    text-align: center;
    font-size: 25px;
    font-weight: 400;
    line-height: 28px;
  }
  .banner--lifestyle .tagline {
    position: absolute;
    left: 450px; right: 0; top: 76px;
    text-align: center;
    font-family: "Cinzel", serif;
    font-size: 11px;
  }
  .promise-band {
    position: absolute;
    left: 512px; right: 0; top: 99px; height: 24px;
    background: var(--white);
    color: var(--ink);
    font-family: "Cinzel", serif;
    font-size: 17px;
    line-height: 24px;
    text-align: center;
  }

  /* features */
  .feature { position: absolute; display: flex; gap: 6px; align-items: flex-start; }
  .feature-mark {
    flex: none;
    width: 24px; height: 24px;
    border-radius: 50%;
    background: var(--badge);
    border: 2px solid var(--white);
  }
  .feature-mark--square { border-radius: 2px; width: 28px; height: 20px; }
  .feature-title {
    font-family: "Cinzel", serif;
    font-size: 11px;
    line-height: 13px;
    text-transform: uppercase;
  }
  .feature-text {
    font-size: 8.5px;
    line-height: 10.5px;
    color: var(--soft);
    white-space: nowrap;
  }

  /* dark banners */
  .brand-panel {
    position: absolute; left: 0; top: 0;
    width: 204px; height: 214px;
    background: var(--panel);
  }
  .brand--panel { left: 0; top: 58px; width: 204px; }
  .banner--doors .headline,
  .banner--accessories .headline { left: 384px; top: 22px; }
  .banner--doors .headline { font-size: 30px; letter-spacing: 0.5px; }
  .banner--accessories .headline { font-size: 23.5px; letter-spacing: 0.3px; top: 25px; }
  .banner--doors .subline,
  .banner--accessories .subline { left: 384px; top: 59px; font-size: 17px; letter-spacing: 5.5px; }
  .banner--doors .feature-title,
  .banner--accessories .feature-title { font-size: 12px; }
  .banner--doors .feature-text,
  .banner--accessories .feature-text { font-size: 9px; line-height: 11px; }
</style>
</head>
<body>

<!-- Banner 1: lifestyle -->
<section class="banner banner--lifestyle">
  <svg class="banner-art" width="1068" height="214" viewBox="0 0 1068 214">
    <defs>
      <linearGradient id="party-a" x1="0" y1="0" x2="1" y2="1">
        <stop offset="0" stop-color="#e9d9b0"/>
        <stop offset="0.5" stop-color="var(--warm-1)"/>
        <stop offset="1" stop-color="#8a6a3e"/>
      </linearGradient>
      <linearGradient id="party-b" x1="0" y1="0" x2="1" y2="1">
        <stop offset="0" stop-color="#f2e6b8"/>
        <stop offset="0.45" stop-color="var(--warm-2)"/>
        <stop offset="1" stop-color="#7a3b2c"/>
      </linearGradient>
    </defs>
    <polygon points="0,0 292,0 234,214 0,214" fill="url(#party-a)" role="img" aria-label="Friends raising drinks over a barbecue table"/>
    <polygon points="298,0 546,0 486,214 240,214" fill="url(#party-b)" role="img" aria-label="Friends sharing food at an outdoor table in the sun"/>
  </svg>

  <div class="brand" style="left:30px; top:74px; width:190px;">
    <div class="brand-name" style="font-size:30px;">Crestline</div>
    <div class="brand-line">outdoor kitchens</div>
  </div>

  <h1 class="headline">Hand Crafted Outdoor<br>Kitchen Accessories.</h1>
  <p class="tagline">“From our family to your family”</p>
  <p class="promise-band">Elegant Design With Durable Construction</p>

  <div class="feature" style="left:547px; top:136px;">
    <span class="feature-mark"></span>
    <div><div class="feature-title">Quality</div><div class="feature-text">Our employees take Pride in their work</div></div>
  </div>
  <div class="feature" style="left:745px; top:136px;">
    <span class="feature-mark feature-mark--square"></span>
    <div><div class="feature-title">Value</div><div class="feature-text">Our doors weigh 10 Pounds<br>More than the competition</div></div>
  </div>
  <div class="feature" style="left:925px; top:136px;">
    <span class="feature-mark feature-mark--square"></span>
    <div><div class="feature-title">Strength</div><div class="feature-text">Offers higher level of<br>Corrosion Resistance</div></div>
  </div>
  <div class="feature" style="left:656px; top:172px;">
    <span class="feature-mark feature-mark--square"></span>
    <div><div class="feature-title">Durability</div><div class="feature-text">Thick and Durable Stainless<br>Steel Construction</div></div>
  </div>
  <div class="feature" style="left:816px; top:172px;">
    <span class="feature-mark"></span>
    <div><div class="feature-title">Peace of Mind</div><div class="feature-text">Your Satisfaction is our highest priority</div></div>
  </div>
</section>

<!-- Banner 2: access doors -->
<section class="banner banner--doors">
  <svg class="banner-art" width="1068" height="214" viewBox="0 0 1068 214">
    <defs>
      <linearGradient id="table-a" x1="0" y1="0" x2="1" y2="1">
        <stop offset="0" stop-color="var(--wood-1)"/>
        <stop offset="1" stop-color="var(--wood-2)"/>
      </linearGradient>
    </defs>
    <rect x="204" y="0" width="864" height="214" fill="url(#table-a)" role="img" aria-label="Steak on a wooden board beside a table full of shared dishes, seen from above"/>
  </svg>
  <div class="brand-panel"></div>
  <div class="brand brand--panel">
    <div class="brand-name">Crestline</div>
    <div class="brand-line">outdoor kitchens</div>
    <div class="brand-quote" style="padding-left:16px;">“From our family<br>&nbsp;to your family”</div>
  </div>

  <h2 class="headline">Hand Crafted BBQ Access Doors</h2>
  <p class="subline">Elegant Design With Durable Construction</p>

  <div class="feature" style="left:384px; top:100px;">
    <span class="feature-mark"></span>
    <div><div class="feature-title">Quality</div><div class="feature-text">Our employees take Pride in their work</div></div>
  </div>
  <div class="feature" style="left:636px; top:100px;">
    <span class="feature-mark feature-mark--square"></span>
    <div><div class="feature-title">Durability</div><div class="feature-text">Thick and Durable Stainless<br>Steel Construction</div></div>
  </div>
  <div class="feature" style="left:846px; top:100px;">
    <span class="feature-mark feature-mark--square"></span>
    <div><div class="feature-title">Strength</div><div class="feature-text">Offers higher level of<br>Corrosion Resistance</div></div>
  </div>
  <div class="feature" style="left:384px; top:154px;">
    <span class="feature-mark feature-mark--square"></span>
    <div><div class="feature-title">Value</div><div class="feature-text">Our doors weigh 10 Pounds<br>More than the competition</div></div>
  </div>
  <div class="feature" style="left:636px; top:154px;">
    <span class="feature-mark"></span>
    <div><div class="feature-title">Peace of Mind</div><div class="feature-text">Your Satisfaction is our highest priority</div></div>
  </div>
</section>

<!-- Banner 3: accessories -->
<section class="banner banner--accessories">
  <svg class="banner-art" width="1068" height="214" viewBox="0 0 1068 214">
    <defs>
      <linearGradient id="table-b" x1="0" y1="0" x2="1" y2="1">
        <stop offset="0" stop-color="var(--wood-1)"/>
        <stop offset="1" stop-color="var(--wood-2)"/>
      </linearGradient>
    </defs>
    <rect x="204" y="0" width="864" height="214" fill="url(#table-b)" role="img" aria-label="Steak on a wooden board beside a table full of shared dishes, seen from above"/>
  </svg>
  <div class="brand-panel"></div>
  <div class="brand brand--panel">
    <div class="brand-name">Crestline</div>
    <div class="brand-line">outdoor kitchens</div>
    <div class="brand-quote" style="padding-left:16px;">“From our family<br>&nbsp;to your family”</div>
  </div>

  <h2 class="headline">Hand Crafted Outdoor Kitchen Accessories</h2>
  <p class="subline">Elegant Design With Durable Construction</p>

  <div class="feature" style="left:384px; top:100px;">
    <span class="feature-mark"></span>
    <div><div class="feature-title">Quality</div><div class="feature-text">Our employees take Pride in their work</div></div>
  </div>
  <div class="feature" style="left:636px; top:100px;">
    <span class="feature-mark feature-mark--square"></span>
    <div><div class="feature-title">Durability</div><div class="feature-text">Thick and Durable Stainless<br>Steel Construction</div></div>
  </div>
  <div class="feature" style="left:846px; top:100px;">
    <span class="feature-mark feature-mark--square"></span>
    <div><div class="feature-title">Strength</div><div class="feature-text">Offers higher level of<br>Corrosion Resistance</div></div>
  </div>
  <div class="feature" style="left:384px; top:154px;">
    <span class="feature-mark feature-mark--square"></span>
    <div><div class="feature-title">Value</div><div class="feature-text">Our doors weigh 10 Pounds<br>More than the competition</div></div>
  </div>
  <div class="feature" style="left:636px; top:154px;">
    <span class="feature-mark"></span>
    <div><div class="feature-title">Peace of Mind</div><div class="feature-text">Your Satisfaction is our highest priority</div></div>
  </div>
</section>

</body>
</html>
```